Kentucky residential recovery center needs a flyer design

We need a flyer design for a 16 bed male residential/inpatient recovery center based in Richmond, Kentucky. The facility provides short term (average 30 day) treatment to those struggling with substace abuse and addiction. The design should communicate trust, assurance, safety.
Our wesite provides more information https://corvalmend.org/treatment-services/residential-treatment/

Target Market(s)

Men (typically 30-50) struggling with substance addiction

```html
<!DOCTYPE html>
<html lang="en">
<head>
<meta charset="utf-8">
<title>Corvalmend Health – Residential Recovery Flyers</title>
<link rel="stylesheet" href="https://fonts.googleapis.com/css2?family=Poppins:wght@400;500;600;700;800&family=Roboto+Slab:wght@600;700;800&family=Open+Sans:wght@400;600;700&display=swap">
<style>
:root{
  --navy:#0d0d7a;
  --green:#05870f;
  --sky:#6ab7ee;
  --charcoal:#2c3136;
  --ink:#333333;
  --stage:#b3b3b3;
  --white:#ffffff;
  --photo-warm:#8a6a4c;
  --photo-wall:#d8cbb8;
}
*{box-sizing:border-box;margin:0;padding:0}
html,body{width:1200px;height:2926px;overflow:hidden;background:var(--stage)}
body{position:relative;font-family:"Poppins",sans-serif;color:var(--ink)}
.flyer{position:absolute;left:108px;width:984px;height:1272px;background:var(--white);overflow:hidden}
.flyer--program{top:114px}
.flyer--results{top:1516px}
.abs{position:absolute}
.shape-layer{position:absolute;left:0;top:0}
.brand{position:absolute;display:flex;align-items:center;gap:10px;font-family:"Poppins",sans-serif;font-weight:700;font-size:22px;color:var(--navy)}
.brand-dot{width:22px;height:22px;border-radius:50%;background:var(--green)}
.photo{position:absolute;background:linear-gradient(160deg,var(--photo-wall),var(--photo-warm))}

/* flyer 1 */
.headline-pill{left:62px;top:186px;width:420px;height:115px;background:var(--green);border-radius:58px 0 0 58px;padding:6px 0 0 32px;color:var(--white);font-weight:800;font-size:30px;line-height:31px;letter-spacing:.5px}
.center-title{left:64px;top:312px;color:var(--white);font-family:"Roboto Slab",serif;font-weight:700;font-size:39px;line-height:39px}
.capacity-lead{left:62px;top:505px;font-size:22px;font-weight:600;color:var(--ink)}
.capacity-pill{left:62px;top:551px;height:40px;width:440px;border:2px solid var(--green);border-radius:20px;display:flex;align-items:center;overflow:hidden}
.capacity-pill .count{background:var(--green);color:var(--white);font-weight:800;font-size:28px;height:100%;padding:0 12px 0 12px;display:flex;align-items:center;border-radius:20px}
.capacity-pill .note{font-family:"Roboto Slab",serif;font-weight:700;font-size:21px;color:var(--navy);padding-left:12px}
.issues-band{left:0;top:814px;width:984px;height:240px}
.issues-tag{left:298px;top:804px;width:388px;height:34px;background:var(--white);border:2px solid var(--sky);border-radius:8px;text-align:center;color:var(--green);font-weight:600;font-size:21px;line-height:30px;letter-spacing:.3px}
.issues-title{left:0;width:984px;top:842px;text-align:center;font-family:"Roboto Slab",serif;font-weight:800;font-size:38px;color:var(--navy)}
.issue-card{top:932px;width:208px;height:96px;background:var(--white);border-radius:10px;display:flex;align-items:flex-end;justify-content:center;padding-bottom:8px;text-align:center;font-weight:600;font-size:21px;line-height:24px;color:#3a3a3a;letter-spacing:.5px}
.issue-icon{top:896px;width:70px;height:70px;border-radius:50%;background:var(--white);border:3px solid var(--sky);display:flex;align-items:center;justify-content:center}
.help-lead{left:0;width:984px;top:1072px;text-align:center;color:var(--green);font-weight:600;font-size:24px}
.help-title{left:0;width:984px;top:1106px;text-align:center;color:var(--navy);font-family:"Roboto Slab",serif;font-weight:700;font-size:37px}
.phone{display:flex;align-items:center;gap:8px;color:var(--white);font-weight:600;font-size:31px}
.contact-lines{left:365px;top:1192px;font-family:"Open Sans",sans-serif;font-size:20px;color:#555;line-height:29px}
.contact-lines div{display:flex;align-items:center;gap:8px}
.follow{left:754px;top:1214px;font-family:"Open Sans",sans-serif;font-weight:700;font-size:15px;color:#333;display:flex;align-items:center;gap:6px}
.follow-dot{width:15px;height:15px;border-radius:50%;background:var(--navy)}
.divider{left:742px;top:1206px;width:1px;height:40px;background:#555}
.cert-badge{left:874px;top:1204px;width:48px;height:48px;border-radius:50%;background:#e3b52c}

/* flyer 2 */
.hero-title{left:47px;width:440px;top:168px;text-align:center;font-weight:800;font-size:63px;line-height:60px;color:var(--white)}
.hero-title .accent{color:var(--green);display:block}
.why-title{left:0;width:984px;top:518px;text-align:center;font-weight:800;font-size:32px;color:var(--navy)}
.why-title span{color:var(--green)}
.why-text{left:70px;width:844px;top:564px;text-align:center;font-weight:600;font-size:19px;line-height:23px;color:var(--ink)}
.feature{top:608px;display:flex;align-items:center;gap:12px;font-weight:600;font-size:16px;line-height:19px;color:var(--navy)}
.feature-icon{width:60px;height:60px;border-radius:50%;border:3px solid var(--sky);display:flex;align-items:center;justify-content:center}
.choose-band{left:284px;top:689px;width:416px;height:50px}
.choose-title{left:284px;top:689px;width:416px;text-align:center;color:var(--white);font-weight:700;font-size:38px;line-height:50px}
.dark-band{left:0;top:814px;width:984px;height:254px}
.stats-card{left:60px;top:739px;width:858px;height:128px;background:var(--white);border-radius:0 0 22px 22px;display:flex}
.stat{flex:1;text-align:center;padding-top:2px;position:relative}
.stat + .stat::before{content:"";position:absolute;left:0;top:10px;height:80px;border-left:2px dotted #9a9a9a}
.stat-num{font-weight:700;font-size:38px;line-height:46px;color:var(--navy)}
.stat-label{font-weight:500;font-size:14px;line-height:16px;color:#333}
.stat-note{font-family:"Open Sans",sans-serif;font-size:10px;line-height:12px;color:#555;margin-top:3px}
.avatar{width:98px;height:98px;border-radius:50%;border:4px solid var(--white);background:linear-gradient(180deg,#9cc3e8,#6d7f5b)}
.quote{font-family:"Open Sans",sans-serif;font-size:13.5px;line-height:18px;color:var(--white)}
.quote-mark{color:var(--green);font-family:"Roboto Slab",serif;font-weight:800;font-size:44px;line-height:30px}
.quote-name{color:var(--green);font-style:italic;font-weight:700;font-size:13px}
.ins-title{left:0;width:984px;top:1070px;text-align:center;font-family:"Roboto Slab",serif;font-weight:600;font-size:32px;color:var(--navy)}
.ins-title span{color:var(--green)}
.ins-row{left:52px;width:880px;top:1124px;display:flex;justify-content:space-between;align-items:center}
.ins-name{font-family:"Poppins",sans-serif;font-weight:600;font-size:17px;color:var(--navy)}
.ins-rule{left:52px;top:1178px;width:880px;height:1px;background:#bbb}
.address{left:364px;top:1189px;display:flex;align-items:center;gap:6px;font-weight:600;font-size:15px;color:var(--navy)}
.transport{left:384px;top:1232px;font-weight:600;font-size:24px;letter-spacing:2px;color:var(--white)}
</style>
</head>
<body>

<!-- Flyer one: the program -->
<section class="flyer flyer--program">
  <svg class="shape-layer" width="984" height="1272" viewBox="0 0 984 1272">
    <path d="M0 0H984V548C900 505 780 470 660 460C460 440 250 480 0 450Z" fill="var(--navy)"/>
    <path d="M0 468C160 500 330 486 480 444" stroke="var(--green)" stroke-width="7" fill="none"/>
    <path d="M700 560C800 525 900 530 984 545V590C900 560 800 565 700 580Z" fill="var(--green)"/>
    <ellipse cx="220" cy="-20" rx="212" ry="168" fill="var(--white)"/>
    <circle cx="702" cy="306" r="282" fill="var(--white)"/>
    <path d="M702 28A278 278 0 0 1 702 584" stroke="var(--green)" stroke-width="12" fill="none"/>
    <path d="M702 584A278 278 0 0 1 702 28" stroke="var(--navy)" stroke-width="12" fill="none"/>
    <path d="M0 1054V814H984V1054" fill="var(--sky)"/>
    <path d="M0 1062 q12 -14 24 0 t24 0 t24 0 t24 0 t24 0 t24 0 t24 0 t24 0 t24 0 t24 0 t24 0 t24 0 t24 0 t24 0 t24 0 t24 0 t24 0 t24 0 t24 0 t24 0 t24 0 t24 0 t24 0 t24 0 t24 0 t24 0 t24 0 t24 0 t24 0 t24 0 t24 0 t24 0 t24 0 t24 0 t24 0 t24 0 t24 0 t24 0 t24 0 t24 0 t24 0 t24 0 V1072 H0Z" fill="var(--white)"/>
    <path d="M0 1176H300C340 1176 350 1220 360 1272H0Z" fill="var(--navy)"/>
    <path d="M300 1176C340 1176 354 1220 366 1268H984" stroke="var(--green)" stroke-width="4" fill="none"/>
  </svg>

  <div class="brand" style="left:118px;top:64px">
    <span class="brand-dot"></span>Corvalmend Health
  </div>

  <div class="photo" role="img" aria-label="Residential lounge with leather sofas, coffee table and patterned rug" style="left:444px;top:48px;width:516px;height:516px;border-radius:50%"></div>

  <div class="abs headline-pill">STRUGGLING WITH<br>SUBSTANCE<br>ADDICTION?</div>
  <div class="abs center-title">MENS<br>RESIDENTIAL<br>RECOVERY CENTER</div>

  <div class="abs capacity-lead">The program has a small capacity of</div>
  <div class="abs capacity-pill"><span class="count">16 MEN</span><span class="note">split into two groups of 8</span></div>

  <div class="photo" role="img" aria-label="Sitting room with a brown leather sofa" style="left:62px;top:618px;width:280px;height:166px;border-radius:16px"></div>
  <div class="photo" role="img" aria-label="Lounge with sofa, desk and rug" style="left:352px;top:618px;width:280px;height:166px;border-radius:16px"></div>
  <div class="photo" role="img" aria-label="Front sign and single-storey building of the recovery center" style="left:644px;top:618px;width:280px;height:166px;border-radius:16px;background:linear-gradient(180deg,#7fb2e8 0%,#9ab8d8 45%,#6f5a48 62%,#6e9a4a 100%)"></div>

  <div class="abs issues-tag">PROBLEMS WE CAN HELP WITH</div>
  <div class="abs issues-title">WHAT ISSUES CAN BE TREATED?</div>

  <div class="abs issue-card" style="left:62px">ALCOHOLISM</div>
  <div class="abs issue-card" style="left:279px">DRUG<br>ADDICTION</div>
  <div class="abs issue-card" style="left:497px">MEDICATION<br>ADDICTION</div>
  <div class="abs issue-card" style="left:714px">BEHAVIORAL<br>HEALTH</div>

  <div class="abs issue-icon" style="left:131px"><svg width="40" height="40" viewBox="0 0 40 40"><circle cx="20" cy="20" r="16" fill="none" stroke="var(--navy)" stroke-width="3"/><rect x="17" y="10" width="6" height="20" rx="2" fill="var(--green)"/><line x1="9" y1="31" x2="31" y2="9" stroke="var(--navy)" stroke-width="3"/></svg></div>
  <div class="abs issue-icon" style="left:348px"><svg width="40" height="40" viewBox="0 0 40 40"><circle cx="17" cy="15" r="6" fill="var(--green)"/><path d="M7 34c0-8 5-12 10-12s10 4 10 12Z" fill="var(--green)"/><circle cx="30" cy="12" r="5" fill="none" stroke="var(--navy)" stroke-width="2.5"/></svg></div>
  <div class="abs issue-icon" style="left:566px"><svg width="40" height="40" viewBox="0 0 40 40"><rect x="6" y="17" width="26" height="7" rx="2" transform="rotate(-40 20 20)" fill="var(--green)"/><line x1="28" y1="10" x2="35" y2="4" stroke="var(--navy)" stroke-width="3"/><line x1="6" y1="32" x2="11" y2="28" stroke="var(--navy)" stroke-width="3"/></svg></div>
  <div class="abs issue-icon" style="left:783px"><svg width="40" height="40" viewBox="0 0 40 40"><circle cx="20" cy="24" r="7" fill="var(--green)"/><circle cx="9" cy="10" r="3.5" fill="var(--navy)"/><circle cx="20" cy="7" r="3.5" fill="var(--navy)"/><circle cx="31" cy="10" r="3.5" fill="var(--navy)"/><rect x="16" y="32" width="8" height="4" fill="var(--navy)"/></svg></div>

  <div class="abs help-lead">Our caring team will help answer any questions you have</div>
  <div class="abs help-title">Get in touch with us now. We're here to help!</div>

  <div class="abs phone" style="left:60px;top:1200px">
    <svg width="24" height="24" viewBox="0 0 24 24"><path d="M6 2l4 4-2 3c1 3 4 6 7 7l3-2 4 4-3 4C10 22 2 14 2 5Z" fill="var(--green)"/></svg>859-555-0148
  </div>

  <div class="abs contact-lines">
    <div><svg width="22" height="18" viewBox="0 0 22 18"><rect x="1" y="2" width="20" height="14" rx="2" fill="var(--green)"/><path d="M2 3l9 7 9-7" stroke="var(--white)" stroke-width="2" fill="none"/></svg>admissions@corvalmend.com</div>
    <div>live chat available at <svg width="20" height="20" viewBox="0 0 20 20"><circle cx="10" cy="10" r="8" fill="none" stroke="var(--green)" stroke-width="2.5"/><path d="M2 10h16M10 2c-4 4-4 12 0 16M10 2c4 4 4 12 0 16" stroke="var(--green)" stroke-width="2" fill="none"/></svg>corvalmend.org</div>
  </div>
  <div class="abs divider"></div>
  <div class="abs follow">follow us on <span class="follow-dot"></span></div>
  <div class="abs cert-badge"></div>
</section>

<!-- Flyer two: results -->
<section class="flyer flyer--results">
  <svg class="shape-layer" width="984" height="1272" viewBox="0 0 984 1272">
    <path d="M0 0H984V540C700 470 350 500 0 560Z" fill="var(--green)"/>
    <path d="M0 565C340 500 700 470 984 540V480C700 420 350 450 0 520Z" fill="var(--navy)"/>
    <path d="M0 575C340 515 700 490 984 555V600H0Z" fill="var(--white)"/>
    <path d="M984 0V440C900 420 760 400 560 450L490 0Z" fill="var(--navy)"/>
    <ellipse cx="230" cy="-20" rx="212" ry="168" fill="var(--white)"/>
    <circle cx="267" cy="259" r="244" fill="var(--white)"/>
    <circle cx="267" cy="259" r="236" fill="var(--navy)"/>
    <path d="M0 814H984V1052H0Z" fill="var(--charcoal)"/>
    <path d="M0 1060 q12 -14 24 0 t24 0 t24 0 t24 0 t24 0 t24 0 t24 0 t24 0 t24 0 t24 0 t24 0 t24 0 t24 0 t24 0 t24 0 t24 0 t24 0 t24 0 t24 0 t24 0 t24 0 t24 0 t24 0 t24 0 t24 0 t24 0 t24 0 t24 0 t24 0 t24 0 t24 0 t24 0 t24 0 t24 0 t24 0 t24 0 t24 0 t24 0 t24 0 t24 0 t24 0 t24 0 V1070 H0Z" fill="var(--white)"/>
    <path d="M290 689H700L684 739H300Z" fill="var(--sky)"/>
    <path d="M0 1179H300C340 1179 350 1222 360 1272H0Z" fill="var(--navy)"/>
    <path d="M320 1229H984V1272H370C360 1250 350 1236 320 1229Z" fill="var(--green)"/>
    <path d="M300 1179C340 1179 354 1224 366 1272" stroke="var(--green)" stroke-width="4" fill="none"/>
  </svg>

  <div class="photo" role="img" aria-label="Lounge with leather sofas, desk, chair and framed art" style="left:510px;top:0;width:474px;height:468px;border-radius:0 0 0 60px"></div>

  <div class="brand" style="left:130px;top:60px">
    <span class="brand-dot"></span>Corvalmend Health
  </div>

  <div class="abs hero-title">ADDICTION TREATMENT <span class="accent">THAT WORKS</span></div>

  <div class="abs why-title">WHY TREATMENT <span>HERE WORKS</span></div>
  <div class="abs why-text">We treat patients the way we would want to be treated which is illustrated by our 95% satisfaction rate from our patients.</div>

  <div class="abs feature" style="left:136px">
    <span class="feature-icon"><svg width="30" height="30" viewBox="0 0 30 30"><rect x="7" y="5" width="16" height="14" rx="2" fill="var(--navy)"/><path d="M15 8v8M11 12h8" stroke="var(--white)" stroke-width="2.5"/><path d="M3 22h16l8-3v5l-8 3H3Z" fill="var(--sky)"/></svg></span>EVIDENCE BASED<br>TREATMENT
  </div>
  <div class="abs feature" style="left:360px">
    <span class="feature-icon"><svg width="30" height="30" viewBox="0 0 30 30"><circle cx="15" cy="7" r="4" fill="var(--navy)"/><path d="M9 26V14h12v12" fill="var(--navy)"/><circle cx="6" cy="12" r="3" fill="var(--green)"/><circle cx="24" cy="12" r="3" fill="var(--green)"/></svg></span>INDIVIDUALIZED
  </div>
  <div class="abs feature" style="left:587px">
    <span class="feature-icon"><svg width="30" height="30" viewBox="0 0 30 30"><circle cx="15" cy="8" r="4" fill="var(--navy)"/><rect x="11" y="13" width="8" height="7" rx="2" fill="var(--navy)"/><path d="M3 16c2 6 6 9 12 10 6-1 10-4 12-10" stroke="var(--green)" stroke-width="3" fill="none"/></svg></span>MEDICATION ASSISTED<br>TREATMENT
  </div>

  <div class="abs choose-title">Why choose us?</div>

  <div class="abs stats-card">
    <div class="stat"><div class="stat-num">100+</div><div class="stat-label">YEARS</div><div class="stat-note">Over 100 years of medical and clinical<br>experience behind our team</div></div>
    <div class="stat"><div class="stat-num">95%</div><div class="stat-label">SATISFACTION<br>RATING</div><div class="stat-note">Our patients rate us 95 out of 100</div></div>
    <div class="stat"><div class="stat-num">#1</div><div class="stat-label">BEST DRUG &amp; ALCOHOL<br>REHAB CENTER</div><div class="stat-note">Voted one of the best Alcohol and<br>Drug rehab centers</div></div>
    <div class="stat"><div class="stat-num">2,500+</div><div class="stat-label">PATIENTS TREATED</div><div class="stat-note">Over 2,500 patients treated<br>successfully and counting</div></div>
  </div>

  <div class="abs avatar" role="img" aria-label="Portrait of a former patient" style="left:58px;top:906px"></div>
  <div class="abs" style="left:190px;top:898px;width:290px">
    <div class="quote-mark">&ldquo;</div>
    <p class="quote">This is a special place. The environment was different, the staff really care about the people that are here. I was able to be comfortable and have an open mind. It changes things for me.</p>
    <span class="quote-name">Dale Whitaker</span> <span class="quote-mark">&rdquo;</span>
  </div>

  <div class="abs avatar" role="img" aria-label="Former patient standing by the center's front sign" style="left:502px;top:906px"></div>
  <div class="abs" style="left:618px;top:888px;width:300px">
    <div class="quote-mark">&ldquo;</div>
    <p class="quote">Life-changing experience. Their staff genuinely cares about the clients. I've been to many programs and my experience there has made me so much stronger as a person. Thanks, Corvalmend Health.</p>
    <span class="quote-name">Marcus Trent</span> <span class="quote-mark">&rdquo;</span>
  </div>

  <div class="abs ins-title">Most Insurances <span>Accepted</span></div>
  <div class="abs ins-row">
    <span class="ins-name">Evenpath</span>
    <span class="ins-name">Harborline</span>
    <span class="ins-name">Crestpoint</span>
    <span class="ins-name">Meridale</span>
    <span class="ins-name">Unityfield</span>
    <span class="ins-name">Ashcrest</span>
    <span class="ins-name">Havenly</span>
    <span class="ins-name">Veridon</span>
    <span class="ins-name">Solace</span>
  </div>
  <div class="abs ins-rule"></div>

  <div class="abs phone" style="left:60px;top:1205px">
    <svg width="24" height="24" viewBox="0 0 24 24"><path d="M6 2l4 4-2 3c1 3 4 6 7 7l3-2 4 4-3 4C10 22 2 14 2 5Z" fill="var(--green)"/></svg>859-555-0148
  </div>
  <div class="abs address">
    <svg width="16" height="18" viewBox="0 0 16 18"><path d="M8 1a6 6 0 0 0-6 6c0 4 6 10 6 10s6-6 6-10a6 6 0 0 0-6-6Z" fill="none" stroke="var(--green)" stroke-width="2"/><circle cx="8" cy="7" r="2" fill="var(--green)"/></svg>1480 Larkmoor Dr
  </div>
  <div class="abs transport">FREE TRANSPORT ASSISTANCE AVAILABLE</div>
</section>

</body>
</html>
```